Aunt Wilma's Ember-Kissed Husk Shack Concession Trailer Logo Wraps

Looking to put my design concept into a final production-ready format for vinyl-based logo "wrap" on the exterior of a 7x12 black concession trailer selling farm-fresh corn on the cob slathered in flavor flamboyance, corn in a cup, corn over crushed snacks (Crunvels, Zaplins, Puffnars, etc.) served in the bags, fire-roasted street corn (Mexican elotes), corn grits, corn chowder, cornbread, corndogs. I have my fonts and colors and a flame graphic I've roughly edited/reworked attempting to make it work and need a design pro to bring it all together for me. The approximate size of the graphics on the four sides of the trailer will be: the serving window when closed (48"L x 24"H); front (48"x48"); full right side (11'x5'); door (6'x2') and possibly the left side next to door (3'x5'). Pictures uploaded.
Target Market(s)
Food truck festivals, private catering gigs, fairs, farm markets, concerts, etc.
Font styles to use
Other font styles liked:
- flame fetish, Algerian
Requirements
Must have
- My color scheme as depicted in uploaded files, flame fetish font uploaded (will consider similar fonts), flame/fire artwork, bright bold colors that pop against a black background
Nice to have
- straight line of flames on each side of the "fire-roasted" text, flowing from the first and last letter

```html
<!DOCTYPE html>
<html lang="en">
<head>
<meta charset="utf-8">
<title>Aunt Wilma's Ember-Kissed Husk Shack</title>
<link rel="stylesheet" href="https://fonts.googleapis.com/css2?family=Abril+Fatface&family=Oswald:wght@600&family=Bungee&family=Nunito:wght@700&display=swap">
<style>
  :root {
    --night: #000000;
    --sky-blue: #2aa6df;
    --corn-yellow: #f6e21c;
    --ember-orange: #ff7a12;
    --flame-red: #d8340a;
    --flame-gold: #ffc83a;
  }
  html, body {
    margin: 0;
    padding: 0;
    width: 1200px;
    height: 554px;
    overflow: hidden;
    background: var(--night);
  }
  .trailer-banner {
    position: relative;
    width: 1200px;
    height: 554px;
    background: var(--night);
    overflow: hidden;
  }
  .flame-art {
    position: absolute;
    top: 80px;
    width: 420px;
    height: 220px;
  }
  .flame-art--left {
    left: 0;
    background:
      radial-gradient(ellipse 60% 80% at 10% 100%, var(--flame-gold) 0%, var(--ember-orange) 35%, var(--flame-red) 60%, transparent 80%),
      radial-gradient(ellipse 60% 45% at 70% 100%, var(--ember-orange) 0%, var(--flame-red) 45%, transparent 75%);
  }
  .flame-art--right {
    right: 0;
    background:
      radial-gradient(ellipse 60% 80% at 90% 100%, var(--flame-gold) 0%, var(--ember-orange) 35%, var(--flame-red) 60%, transparent 80%),
      radial-gradient(ellipse 60% 45% at 30% 100%, var(--ember-orange) 0%, var(--flame-red) 45%, transparent 75%);
  }
  .flame-reflection {
    position: absolute;
    left: 0;
    top: 300px;
    width: 1200px;
    height: 90px;
    background: linear-gradient(180deg, rgba(216, 110, 20, 0.35) 0%, rgba(0, 0, 0, 0) 100%);
  }
  .horizon-line {
    position: absolute;
    left: 0;
    top: 299px;
    width: 1200px;
    height: 1px;
    background: #1a1a1a;
  }
  .wordmark {
    position: absolute;
    inset: 0;
  }
  .owner-name {
    font-family: "Abril Fatface", serif;
    fill: var(--sky-blue);
  }
  .cooking-style {
    font-family: "Oswald", sans-serif;
    font-weight: 600;
    fill: var(--flame-gold);
  }
  .cooking-rule {
    stroke: var(--flame-gold);
    stroke-width: 3;
  }
  .shack-name {
    font-family: "Bungee", sans-serif;
    fill: var(--corn-yellow);
  }
  .tagline {
    font-family: "Nunito", sans-serif;
    font-weight: 700;
    fill: var(--sky-blue);
  }
</style>
</head>
<body>
  <main class="trailer-banner">
    <div class="flame-art flame-art--left" role="img" aria-label="Flame artwork rising on the left side"></div>
    <div class="flame-art flame-art--right" role="img" aria-label="Flame artwork rising on the right side"></div>
    <div class="flame-reflection" role="img" aria-label="Glossy reflection of the flames"></div>
    <div class="horizon-line"></div>

    <svg class="wordmark" width="1200" height="554" viewBox="0 0 1200 554">
      <text class="owner-name" x="600" y="172" text-anchor="middle" font-size="120"
            textLength="820" lengthAdjust="spacingAndGlyphs">Aunt Wilma's</text>

      <line class="cooking-rule" x1="330" y1="251" x2="370" y2="251"/>
      <text class="cooking-style" x="600" y="272" text-anchor="middle" font-size="56"
            textLength="440" lengthAdjust="spacingAndGlyphs">EMBER-KISSED</text>
      <line class="cooking-rule" x1="830" y1="251" x2="870" y2="251"/>

      <text class="shack-name" x="600" y="440" text-anchor="middle" font-size="130"
            textLength="980" lengthAdjust="spacingAndGlyphs">HUSK SHACK</text>

      <text class="tagline" x="600" y="512" text-anchor="middle" font-size="34"
            textLength="800" lengthAdjust="spacingAndGlyphs">Farm-fresh cobs dressed in bold, smoky seasoning!</text>
    </svg>
  </main>
</body>
</html>
```